Web Design Project

We are an IT System Integrator. We provide Korvin 450 ERP System, CRM etc. We also provide hardware, networking servicing. Please look at www.zolvantix.com.sg. They provide the same service as us. We like to redesign our web site. I will attached the color that I prefer for reference.

Our website is www.tadurk.com.sg.  It has been created about 14 years ago.  We are trying to revamp it with a new look and information.   The new website must be informative, fast.    I have attached an attachment which show the color that I prefer(brownish golden).   

Our competitor (www.zolvantix.com) is carrying the same trade as us.  They have all the informations In their website that we will like to have.  Therefore I recommend you to take a look at my competitor website and have a better   
understanding on the kind of information I would like to have for my new website.

This project is guarantee to the person with the best design.  We can have it guarantee.

Target Market(s)

Corporate and companies

Industry/Entity Type

Hardware

```html
<!DOCTYPE html>
<html lang="en">
<head>
<meta charset="utf-8">
<title>Norvell Information Systems – Products</title>
<link rel="stylesheet" href="https://fonts.googleapis.com/css2?family=Ubuntu:wght@300;400;500;700&family=Arimo:wght@400&display=swap">
<style>
:root{
  --page:#e9e9eb;
  --panel:#f6f6f8;
  --gold:#c8862a;
  --gold-link:#b8853e;
  --brown:#8a6a2c;
  --brown-dark:#6a4e1c;
  --footer:#7e5f28;
  --footer-edge:#b89a5c;
  --ink:#222;
  --muted:#777;
  --nav-ink:#5a3e10;
}
*{margin:0;padding:0;box-sizing:border-box}
html,body{width:1190px;height:1200px;overflow:hidden}
body{position:relative;background:radial-gradient(ellipse at 50% 25%,#f7f7f8 0%,var(--page) 70%);font-family:"Arimo",Arial,sans-serif;color:var(--ink)}
a{text-decoration:none;color:inherit}
.abs{position:absolute}

/* header */
.brand{left:140px;top:24px;display:flex;align-items:center;gap:14px}
.brand-mark{width:118px;height:96px;border-radius:50%;background:radial-gradient(circle at 40% 35%,#f2d48a,#c8862a 70%)}
.brand-name{font-family:"Ubuntu",sans-serif;font-weight:500;font-size:13.5px;line-height:26px;color:var(--gold);letter-spacing:.3px}
.util-nav{left:500px;top:20px;font-size:10.5px;color:var(--muted);display:flex;gap:14px}
.util-nav span.sep{color:#aaa}

.main-nav{left:0;top:133px;width:1190px;height:40px}
.main-nav .rule{position:absolute;left:230px;top:7px;width:730px;height:2px;background:linear-gradient(90deg,transparent,#c9c9c9 20%,#c9c9c9 80%,transparent)}
.main-nav ul{list-style:none;position:absolute;left:320px;top:0;display:flex;height:38px}
.main-nav li{font-family:"Ubuntu",sans-serif;font-weight:500;font-size:12.5px;color:var(--nav-ink);padding:14px 13px 0;height:38px}
.main-nav li.active{background:var(--brown);color:#fff;border-radius:4px 4px 0 0}

/* slider */
.slide-art{left:160px;top:180px;width:390px;height:340px;border-radius:50%;background:radial-gradient(ellipse at 50% 50%,#d8d8da 0%,#eaeaec 55%,transparent 72%)}
.slide-text{left:526px;top:238px;width:470px;font-family:"Ubuntu",sans-serif;font-weight:300;font-size:23.5px;line-height:41.5px;color:#222}
.slide-text em{font-style:normal;color:var(--gold)}
.slide-arrow{top:320px}
.slide-dots{left:530px;top:523px;display:flex;gap:10px}
.slide-dots i{display:block;width:35px;height:8px;border-radius:4px;background:#fafafa;box-shadow:0 1px 2px rgba(0,0,0,.3)}
.slide-dots i.on{background:#c49a4c}

/* products panel */
.panel{left:173px;top:583px;width:830px;height:383px;background:var(--panel);border:1px solid #d9d9dc}
.panel-tab{left:185px;top:574px;width:131px;height:33px;background:linear-gradient(#9a7836,var(--brown-dark));border-radius:6px 6px 0 0;color:#fff;font-family:"Ubuntu",sans-serif;font-weight:500;font-size:20px;padding:3px 0 0 23px}
.thumb{border-radius:6px;background:linear-gradient(135deg,#dfe9f2,#8fb3d0)}
.heading{font-family:"Ubuntu",sans-serif;font-size:15px;color:var(--gold-link)}
.copy{font-size:11.8px;line-height:18px;color:#333}
.lead{font-size:14px;color:#333}
.prod-link{font-family:"Ubuntu",sans-serif;font-size:14.5px;color:var(--gold-link);text-decoration:underline;text-underline-offset:3px}

/* news */
.news{left:133px;top:1000px;width:924px;height:42px;background:#fff;box-shadow:0 8px 10px -6px rgba(0,0,0,.25)}
.news-label{position:absolute;left:0;top:0;height:42px;width:165px;background:linear-gradient(#9a9a9a,#7d7d7d);color:#fff;font-family:"Ubuntu",sans-serif;font-weight:500;font-size:15.5px;padding:12px 0 0 41px}
.news-label svg{position:absolute;left:6px;top:7px}
.news-tip{position:absolute;left:165px;top:0}
.news-text{position:absolute;left:175px;top:13px;font-size:11.5px;color:#333;border-bottom:1px dashed #ccc;width:680px;padding-bottom:8px}
.news-go{position:absolute;right:10px;top:11px}

/* footer */
.footer{left:0;top:1080px;width:1190px;height:120px;background:var(--footer);border-top:4px solid var(--footer-edge)}
.footer-nav{position:absolute;left:293px;top:16px;display:flex;gap:16px;color:#fff;font-size:13px}
.footer-nav .sep{color:#e6d7b8}
.social{position:absolute;left:547px;top:40px;display:flex;gap:7px}
.social span{width:29px;height:29px;border-radius:4px;background:#4f7fb5}
.social span:nth-child(2){background:#5cc0de}
.social span:nth-child(3){background:#2d77b3}
.copyright{position:absolute;left:0;width:1190px;top:89px;text-align:center;color:#fff;font-size:13px}
</style>
</head>
<body>

<header>
  <div class="abs brand">
    <div class="brand-mark"></div>
    <div class="brand-name">NORVELL<br>INFORMATION<br>SYSTEMS PTE LTD</div>
  </div>
  <nav class="abs util-nav">
    <a>HOME</a><span class="sep">|</span><a>SITEMAP</a><span class="sep">|</span><a>LOG INCIDENT</a><span class="sep">|</span><a>ENQUIRY</a><span class="sep">|</span><a>CONTACT</a><span class="sep">|</span><a>CLIENT SUPPORT</a>
  </nav>
  <nav class="abs main-nav">
    <div class="rule"></div>
    <ul>
      <li>COMPANY</li><li class="active">PRODUCTS</li><li>LEDGRA</li><li>SERVICES</li><li style="padding-left:18px">CLIENTELE</li><li style="padding-left:17px">CAREERS</li><li style="padding-left:17px">INFOBIN</li>
    </ul>
  </nav>
</header>

<section class="slider">
  <div class="abs slide-art" role="img" aria-label="Illustration of four figures assembling coloured puzzle pieces"></div>
  <p class="abs slide-text">For more than 20 years, <em>LEDGRA</em> has provided reliable software solutions optimized to take advantage of new technologies and meet the unique requirements of companies.</p>
  <svg class="abs slide-arrow" style="left:135px" width="32" height="32" viewBox="0 0 32 32"><circle cx="16" cy="16" r="14.5" fill="none" stroke="#8a6a2c" stroke-width="2"/><path d="M18.5 9 L12 16 L18.5 23" fill="none" stroke="#8a6a2c" stroke-width="2"/></svg>
  <svg class="abs slide-arrow" style="left:1024px" width="32" height="32" viewBox="0 0 32 32"><circle cx="16" cy="16" r="14.5" fill="none" stroke="#8a6a2c" stroke-width="2"/><path d="M13.5 9 L20 16 L13.5 23" fill="none" stroke="#8a6a2c" stroke-width="2"/></svg>
  <div class="abs slide-dots"><i></i><i></i><i class="on"></i></div>
</section>

<main>
  <div class="abs panel"></div>
  <div class="abs panel-tab">Products</div>

  <div class="abs thumb" style="left:195px;top:620px;width:100px;height:75px" role="img" aria-label="Network of connected computers and devices"></div>
  <h3 class="abs heading" style="left:303px;top:624px">Overview</h3>
  <p class="abs copy" style="left:305px;top:647px;width:670px">NIS can assemble a simple computer to fit your exact needs, or craft an entire network that suits your businesses. We are able to provide all computer related products at very competitive prices.</p>

  <p class="abs lead" style="left:199px;top:709px">Some of this Products Include :</p>

  <a class="abs prod-link" style="left:199px;top:738px">Workstations</a>
  <div class="abs thumb" style="left:200px;top:768px;width:92px;height:54px" role="img" aria-label="Desktop workstation with monitor and speakers"></div>
  <p class="abs copy" style="left:305px;top:760px;width:670px">Every environment has its own unique requirements. For instance, one may need more processing power for interactive tasks, visual simulation, and rendering. Another may need affordable performance for business applications. While still another needs hassle-free thin clients for heads-down applications or as front ends to a technical server farm. Whatever your requirement, we have a desktop to meet it.</p>

  <a class="abs prod-link" style="left:199px;top:849px">Servers</a>
  <a class="abs prod-link" style="left:199px;top:879px">Printers</a>
  <a class="abs prod-link" style="left:199px;top:910px">Surveillance Camera</a>
</main>

<aside class="abs news">
  <div class="news-label">
    <svg width="29" height="29" viewBox="0 0 29 29"><rect width="29" height="29" rx="5" fill="#e8a33a"/><circle cx="8" cy="21" r="2.6" fill="#fff"/><path d="M6 13 A10 10 0 0 1 16 23" fill="none" stroke="#fff" stroke-width="2.8"/><path d="M6 7 A16 16 0 0 1 22 23" fill="none" stroke="#fff" stroke-width="2.8"/></svg>
    LATEST NEWS
  </div>
  <svg class="news-tip" width="16" height="42" viewBox="0 0 16 42"><path d="M0 0 L15 21 L0 42 Z" fill="#8a8a8a"/></svg>
  <p class="news-text">Lorem Ipsum is simply dummy text of the printing and typesetting industry.Duis aute irure dolor in reprehenderit in voluptate velit...</p>
  <svg class="news-go" width="22" height="21" viewBox="0 0 22 21"><rect width="22" height="21" rx="3" fill="#c8862a"/><path d="M8 5 L15 10.5 L8 16 Z" fill="#fff"/></svg>
</aside>

<footer class="abs footer">
  <nav class="footer-nav">
    <a>Company</a><span class="sep">|</span><a>Products</a><span class="sep">|</span><a>LEDGRA</a><span class="sep">|</span><a>Services</a><span class="sep">|</span><a>Clientele</a><span class="sep">|</span><a>Careers</a><span class="sep">|</span><a>Infobin</a>
  </nav>
  <div class="social">
    <span role="img" aria-label="Social link one"></span>
    <span role="img" aria-label="Social link two"></span>
    <span role="img" aria-label="Social link three"></span>
  </div>
  <p class="copyright">© Copyrights 2013. Norvell Information Systems. All Rights Reserved.</p>
</footer>

</body>
</html>
```